Federal IT Consulting Company - Brisolux Consulting Group

We're seeking a skilled web designer to create a modern, bold, and engaging WordPress website for Brisolux Consulting Group, LLC. Our company specializes in federal IT consulting, and our name is a play on "Brightening Solutions." The website should reflect our expertise in the federal technology marketplace and position us as a trusted partner for clients navigating their IT journey.

contact: info@brisoluxgrp-example.com

Current Status

WordPress is already installed on our hosting account
We have an existing logo (may need modernization)

Design Requirements

Style:

Modern and visually striking design
Bold elements to convey confidence and expertise
Incorporate the concept of "brightening solutions" into the design

Features:

Modern UX sliders for dynamic content presentation
Eye-catching, high-quality images (stock photos to be sourced by the designer)
Responsive design for all devices

Color Scheme:

To be proposed by the designer, should align with our brand and convey trust and technological expertise

Logo:

Evaluate our current logo
Create a transparent background version if needed
Propose modernization if deemed necessary

Accessibility:

Ensure design elements are accessible to users with disabilities
Use high contrast ratios for text and background colors
Provide text alternatives for non-text content

Website Structure
Create the following pages, with the possibility of subpages:

Home
Services
About
Contact

Specific Page Requirements
Home Page

Striking hero section with a clear value proposition
Overview of our services
Client testimonials or trust indicators

Services Page

Detailed list of our IT consulting services
Clear explanation of how we help navigate the federal IT landscape

About Page

Company history and mission
Team highlights (if applicable)
Our approach to federal IT consulting

Contact Page

Contact form
Other contact methods (phone, email)

Technical Requirements

Fully responsive design
SEO best practices implemented
Fast loading times
Integration with necessary plugins (to be discussed)
Training on how to update and maintain the site
Full compliance with Web Content Accessibility Guidelines (WCAG) 2.1 Level AA
Adherence to Section 508 standards for federal website accessibility
Implementation of necessary features for ADA compliance
Updates

Designs look the same

Target Market(s)

US Federal Govt customers looking for IT support.

Industry/Entity Type

IT Consulting

Coding

Coded - Design and coding required

Colors
0054AA
0677BA
7BADD7
CADEEF
E8F1F8
0094D4
00A9DD
6FCCEA
C7EBF8
E9F6FB
00AB8E
00BBA5
67D7C9
C6EFE9
E9F9F6

```html
<!DOCTYPE html>
<html lang="en">
<head>
<meta charset="utf-8">
<title>Contact Us – Brisolux Consulting Group</title>
<link rel="stylesheet" href="https://fonts.googleapis.com/css2?family=Exo+2:wght@700;800&family=Figtree:wght@400;500;600&display=swap">
<style>
  :root {
    --navy: #2c2a6d;
    --navy-deep: #13123f;
    --accent: #7b76d8;
    --ink: #111111;
    --field: #efefef;
    --field-text: #6e6e6e;
    --white: #ffffff;
    --map: #e9e8e3;
  }
  * { box-sizing: border-box; margin: 0; padding: 0; }
  html, body { width: 793px; height: 1200px; overflow: hidden; }
  body { position: relative; background: var(--white); font-family: "Figtree", sans-serif; color: var(--ink); }
  .abs { position: absolute; }

  /* Header */
  .site-header { position: absolute; left: 0; top: 0; width: 793px; height: 46px; background: var(--white); }
  .brand { position: absolute; display: flex; align-items: center; gap: 6px; font-family: "Figtree", sans-serif; font-weight: 600; }
  .brand-mark { border-radius: 50%; flex: none; }
  .header-brand { left: 94px; top: 11px; font-size: 12px; color: var(--navy); }
  .header-brand .brand-mark { width: 22px; height: 22px; background: var(--navy); }
  .main-nav a { position: absolute; top: 17px; font-size: 8.5px; color: var(--ink); text-decoration: none; font-weight: 500; }
  .btn { background: var(--navy); color: var(--white); border-radius: 14px; font-size: 8.5px; font-weight: 600; display: flex; align-items: center; justify-content: center; text-decoration: none; }
  .nav-cta { position: absolute; left: 619px; top: 10px; width: 81px; height: 26px; }

  /* Hero */
  .hero { position: absolute; left: 0; top: 46px; width: 793px; height: 187px;
    background: linear-gradient(90deg, #eceeef 0%, #e4e7ea 35%, #c9d3dc 55%, #dfe3e6 75%, #b9c3c8 100%); }
  .hero-title { position: absolute; left: 94px; top: 110px; font-family: "Exo 2", sans-serif; font-weight: 800; font-size: 23px; color: var(--ink); }
  .breadcrumb { position: absolute; left: 94px; top: 146px; font-family: "Exo 2", sans-serif; font-weight: 700; font-size: 9.5px; display: flex; align-items: center; gap: 4px; }
  .breadcrumb .current { color: var(--accent); }

  /* Section heading */
  .section-title { position: absolute; left: 0; width: 793px; top: 280px; text-align: center; font-family: "Exo 2", sans-serif; font-weight: 800; font-size: 22px; }
  .hl { color: var(--accent); }
  .rule { position: absolute; height: 2px; background: var(--navy); }

  /* Details card */
  .details-card { position: absolute; left: 94px; top: 357px; width: 261px; height: 261px; background: var(--navy); border-radius: 10px; color: var(--white); }
  .card-title { position: absolute; left: 32px; top: 25px; font-family: "Exo 2", sans-serif; font-weight: 800; font-size: 15.5px; }
  .card-title .dark { color: var(--white); }
  .card-rule { left: 32px; top: 47px; width: 37px; height: 1.5px; background: var(--white); }
  .detail { position: absolute; left: 32px; display: flex; align-items: center; gap: 9px; font-size: 10px; line-height: 14.5px; }
  .detail-icon { width: 26px; height: 26px; border-radius: 50%; background: var(--white); display: flex; align-items: center; justify-content: center; flex: none; }

  /* Form */
  .form-title { position: absolute; left: 404px; top: 365px; font-family: "Exo 2", sans-serif; font-weight: 800; font-size: 15.5px; }
  .field { position: absolute; background: var(--field); border-radius: 4px; font-size: 8.5px; color: var(--field-text); padding: 10px 9px; }
  .submit { position: absolute; left: 404px; top: 592px; width: 80px; height: 26px; }

  /* Map */
  .map { position: absolute; left: 94px; top: 674px; width: 606px; height: 250px; background: var(--map); }

  /* Footer */
  .site-footer { position: absolute; left: 0; top: 980px; width: 793px; height: 220px; background: var(--navy-deep); color: var(--white); }
  .footer-brand { left: 94px; top: 33px; font-size: 15px; color: var(--white); }
  .footer-brand .brand-mark { width: 30px; height: 30px; border: 3px solid var(--white); }
  .col-title { position: absolute; top: 48px; font-family: "Figtree", sans-serif; font-weight: 600; font-size: 10.5px; color: var(--accent); }
  .col-link { position: absolute; font-size: 8.5px; color: var(--white); }
  .foot-info { position: absolute; left: 563px; display: flex; align-items: flex-start; gap: 7px; font-size: 8.5px; line-height: 11.5px; }
  .foot-rule { left: 94px; top: 176px; width: 606px; height: 0.5px; background: rgba(255,255,255,0.35); }
  .copyright { position: absolute; left: 94px; top: 192px; font-size: 8.5px; }
  .social { position: absolute; top: 188px; width: 20px; height: 20px; border-radius: 50%; background: var(--accent); }
</style>
</head>
<body>

<header class="site-header">
  <div class="brand header-brand"><span class="brand-mark"></span>Brisolux Consulting Group</div>
  <nav class="main-nav">
    <a href="#" style="left:451px">Home</a>
    <a href="#" style="left:500px">About Us</a>
    <a href="#" style="left:561px">Services</a>
  </nav>
  <a href="#" class="btn nav-cta">Contact Us</a>
</header>

<section class="hero" role="img" aria-label="Photo of the US Capitol dome under a cloudy sky with trees at the right"></section>
<h1 class="hero-title">CONTACT US</h1>
<div class="breadcrumb">
  <span>HOME</span>
  <svg width="9" height="8" viewBox="0 0 9 8"><path d="M1 1l3 3-3 3M5 1l3 3-3 3" fill="none" stroke="#111" stroke-width="1.4"/></svg>
  <span class="current">CONTACT US</span>
</div>

<h2 class="section-title"><span class="hl">CONTACT</span> US</h2>
<div class="rule" style="left:374px;top:308px;width:45px"></div>

<aside class="details-card">
  <h3 class="card-title"><span class="hl">CONTACT</span> <span class="dark">DETAILS</span></h3>
  <div class="abs card-rule"></div>
  <div class="detail" style="top:73px">
    <span class="detail-icon"><svg width="13" height="14" viewBox="0 0 13 14"><path d="M6.5 1a3.5 3.5 0 0 0-3.5 3.5c0 2.6 3.5 6 3.5 6s3.5-3.4 3.5-6A3.5 3.5 0 0 0 6.5 1z" fill="#7b76d8"/><circle cx="6.5" cy="4.5" r="1.3" fill="#fff"/><ellipse cx="6.5" cy="12" rx="5" ry="1.5" fill="none" stroke="#7b76d8"/></svg></span>
    <span>123 Lorem Ipsum Dummy,<br>#567 Dummy Road 1234</span>
  </div>
  <div class="detail" style="top:114px">
    <span class="detail-icon"><svg width="14" height="10" viewBox="0 0 14 10"><rect width="14" height="10" rx="1.5" fill="#7b76d8"/><path d="M1 1l6 4.5L13 1" fill="none" stroke="#fff" stroke-width="1.2"/></svg></span>
    <span>info@brisoluxgrp-example.com</span>
  </div>
  <div class="detail" style="top:154px">
    <span class="detail-icon"><svg width="13" height="13" viewBox="0 0 13 13"><path d="M3 1l2 3-1.2 1.3a7 7 0 0 0 3.9 3.9L9 8l3 2-1 2C5.5 12 1 7.5 1 2z" fill="#7b76d8"/></svg></span>
    <span>123-456-7890</span>
  </div>
</aside>

<h3 class="form-title"><span class="hl">CONTACT</span> FORM</h3>
<div class="rule" style="left:404px;top:388px;width:37px;height:1.5px"></div>

<form>
  <div class="field" style="left:404px;top:414px;width:142px;height:27px">First Name*</div>
  <div class="field" style="left:556px;top:414px;width:143px;height:27px">Last Name*</div>
  <div class="field" style="left:404px;top:451px;width:142px;height:27px">Email*</div>
  <div class="field" style="left:556px;top:451px;width:143px;height:27px">Phone</div>
  <div class="field" style="left:404px;top:488px;width:295px;height:87px">Message</div>
  <a href="#" class="btn submit">Submit Now</a>
</form>

<div class="map" role="img" aria-label="Road map of the surrounding area with a location pin marking the office"></div>

<footer class="site-footer">
  <div class="brand footer-brand"><span class="brand-mark"></span>Brisolux Consulting Group</div>

  <h4 class="col-title" style="left:338px;top:51px">Quick Links</h4>
  <span class="col-link" style="left:338px;top:76px">Home</span>
  <span class="col-link" style="left:338px;top:93px">About Us</span>
  <span class="col-link" style="left:338px;top:110px">Services</span>

  <h4 class="col-title" style="left:445px">Resources</h4>
  <span class="col-link" style="left:445px;top:74px">Privacy Policy</span>
  <span class="col-link" style="left:445px;top:91px">Terms Of Service</span>

  <h4 class="col-title" style="left:563px">Contact Info</h4>
  <div class="foot-info" style="top:76px">
    <svg width="11" height="13" viewBox="0 0 13 14"><path d="M6.5 1a3.5 3.5 0 0 0-3.5 3.5c0 2.6 3.5 6 3.5 6s3.5-3.4 3.5-6A3.5 3.5 0 0 0 6.5 1z" fill="#7b76d8"/><circle cx="6.5" cy="4.5" r="1.3" fill="#13123f"/><ellipse cx="6.5" cy="12" rx="5" ry="1.5" fill="none" stroke="#7b76d8"/></svg>
    <span>123 Lorem Ipsum Dummy,<br>#567 Dummy Road 1234</span>
  </div>
  <div class="foot-info" style="top:104px">
    <svg width="11" height="8" viewBox="0 0 14 10"><rect width="14" height="10" rx="1.5" fill="#7b76d8"/><path d="M1 1l6 4.5L13 1" fill="none" stroke="#13123f" stroke-width="1.2"/></svg>
    <span>Info@Brisoluxgrp-example.com</span>
  </div>
  <div class="foot-info" style="top:126px">
    <svg width="11" height="11" viewBox="0 0 13 13"><path d="M3 1l2 3-1.2 1.3a7 7 0 0 0 3.9 3.9L9 8l3 2-1 2C5.5 12 1 7.5 1 2z" fill="#7b76d8"/></svg>
    <span>123-456-7890</span>
  </div>

  <div class="abs foot-rule"></div>
  <p class="copyright">© 2024 Brisolux Consulting Group. All rights reserved.</p>
  <span class="social" style="left:600px" aria-label="Social profile 1"></span>
  <span class="social" style="left:626px" aria-label="Social profile 2"></span>
  <span class="social" style="left:653px" aria-label="Social profile 3"></span>
  <span class="social" style="left:680px" aria-label="Social profile 4"></span>
</footer>

</body>
</html>
```